Tall fern bicycle rental

would like to have a bicycle rental website that has the ability to have a calender and be able to sign a liability waiver and pay all on line, We rent fat tire vorn bicycles

```html
<!DOCTYPE html>
<html lang="en">
<head>
<meta charset="utf-8">
<title>Tall Fern Bicycle Rental</title>
<link rel="stylesheet" href="https://fonts.googleapis.com/css2?family=Exo+2:wght@400;500;600;700&family=Lato:wght@400;700&display=swap">
<style>
:root{
  --blue:#1d6db7;
  --blue-dark:#13558f;
  --navy:#0f3f6e;
  --green:#5ba63a;
  --ink:#222;
  --body:#444;
  --grey-bg:#f3f3f3;
  --footer:#1c1c1c;
  --white:#fff;
}
*{box-sizing:border-box;margin:0;padding:0}
html,body{width:1200px;height:4736px;overflow:hidden}
body{position:relative;font-family:"Lato",sans-serif;color:var(--body);background:var(--white)}
.section{position:absolute;left:0;width:1200px;overflow:hidden}
.abs{position:absolute}
.heading{font-family:"Exo 2",sans-serif;font-weight:600;color:var(--ink);text-transform:uppercase}
.rule{position:absolute;width:56px;height:4px;background:var(--blue);left:572px}
.photo{position:absolute}

/* hero */
.hero{top:0;height:755px}
.hero-photo{inset:0;background:linear-gradient(180deg,#4f6a86 0%,#7c93a6 30%,#8a8d86 55%,#6b5d4b 80%,#4c4337 100%)}
.brand{left:145px;top:40px;display:flex;align-items:center;gap:12px}
.brand-dot{width:46px;height:46px;border-radius:50%;background:var(--white)}
.brand-name{font-family:"Exo 2",sans-serif;font-weight:700;color:var(--white);font-size:22px;line-height:1.05;text-transform:uppercase}
.tollfree{left:478px;top:38px;display:flex;align-items:center;gap:10px;color:var(--white)}
.tollfree .ico{width:34px;height:34px;border-radius:50%;background:var(--blue);display:flex;align-items:center;justify-content:center}
.tollfree small{display:block;font-size:11px}
.tollfree b{font-family:"Exo 2",sans-serif;font-size:22px;font-weight:500}
.search{left:686px;top:40px;width:233px;height:34px;border-radius:17px;background:var(--white);font-size:11px;color:#999;padding:10px 16px}
.search svg{position:absolute;right:12px;top:9px}
.signup{left:937px;top:38px;width:120px;height:36px;border-radius:18px;background:var(--blue);color:var(--white);font-family:"Exo 2",sans-serif;font-weight:600;font-size:15px;text-align:center;line-height:36px}
.nav{font-family:"Exo 2",sans-serif;font-weight:600;font-size:15px;color:var(--white);text-transform:uppercase}
.nav a{color:inherit;text-decoration:none;position:absolute;white-space:nowrap}
.nav a.active{color:#6cb6f2}
.hero-title{left:0;width:1200px;top:318px;text-align:center;color:var(--white);font-family:"Exo 2",sans-serif}
.hero-title h1{font-size:76px;font-weight:700;line-height:1.1;text-transform:uppercase}
.hero-tag{font-size:26px;font-weight:500;margin-top:10px}
.dots{left:566px;top:654px;display:flex;gap:8px}
.dots span{width:18px;height:18px;border-radius:50%;border:2px solid var(--white)}
.dots span.on{background:var(--white)}

/* welcome */
.welcome{top:755px;height:602px}
.welcome-bg{inset:0;background:linear-gradient(180deg,#ffffff 0%,#eef2f5 45%,#c9d3da 80%,#aebbc4 100%)}
.welcome-mark{left:147px;top:81px;width:386px;height:386px;border-radius:50%;background:var(--blue);display:flex;align-items:center;justify-content:center;color:var(--white);font-family:"Exo 2",sans-serif;font-weight:700;font-size:44px;text-align:center;line-height:1.05;text-transform:uppercase}
.welcome h2{left:592px;top:105px;font-size:37px;line-height:1.12}
.welcome h2 span{color:var(--blue);display:block}
.welcome .rule{left:592px;top:206px}
.welcome p{left:592px;top:228px;width:470px;font-size:14.5px;line-height:22.5px;color:#333}
.btn-outline{position:absolute;border:3px solid var(--navy);border-radius:22px;color:var(--navy);font-family:"Exo 2",sans-serif;font-weight:700;font-size:15px;text-align:center;text-transform:uppercase}
.welcome .btn-outline{left:592px;top:410px;width:149px;height:40px;line-height:34px}

/* rentals */
.rentals{top:1357px;height:775px;background:linear-gradient(180deg,#1e5f91 0%,#1b6aa8 45%,#1f70b5 100%)}
.rentals-photo{left:0;top:240px;width:1200px;height:420px;background:radial-gradient(ellipse at 20% 60%,rgba(20,50,80,.55),transparent 60%),radial-gradient(ellipse at 85% 40%,rgba(20,50,80,.4),transparent 55%)}
.rentals h2{left:0;width:1200px;top:68px;text-align:center;color:var(--white);font-size:37px}
.card{position:absolute;top:178px;width:294px;height:422px;background:var(--white);text-align:center;box-shadow:0 4px 14px rgba(0,0,0,.2)}
.card-photo{position:absolute;left:0;top:0;width:294px;height:180px;clip-path:polygon(0 0,100% 0,100% 78%,50% 100%,0 78%)}
.card-icon{position:absolute;left:126px;top:166px;width:42px;height:42px;border-radius:50%;background:var(--blue);border:3px solid var(--white);display:flex;align-items:center;justify-content:center}
.card h3{position:absolute;left:0;width:100%;top:232px;font-family:"Exo 2",sans-serif;font-weight:700;font-size:16px;color:var(--ink)}
.card .price{position:absolute;left:0;width:100%;top:257px;font-family:"Exo 2",sans-serif;font-weight:600;font-size:15px;color:var(--blue)}
.card p{position:absolute;left:30px;width:234px;top:285px;font-size:13.5px;line-height:21px;color:#444}
.card .btn-outline{left:80px;top:359px;width:134px;height:36px;line-height:30px;font-size:13px}

/* why */
.why{top:2132px;height:708px}
.why-bg{inset:0;background:linear-gradient(180deg,#ffffff 0%,#f3f5f7 40%,#dde3e8 62%,#7f8d99 80%,#5a4a3b 92%,#3c3128 100%)}
.why-rider{left:1010px;top:210px;width:190px;height:300px;background:linear-gradient(180deg,#6b6b4a,#2f2f2a);border-radius:40px 0 0 40px;opacity:.85}
.why h2{left:0;width:1200px;top:86px;text-align:center;font-size:34px}
.why .sub{left:0;width:1200px;top:142px;text-align:center;font-size:18px;color:#333}
.why .rule{top:190px}
.feature{position:absolute;width:240px;height:240px;border-radius:50%;background:radial-gradient(circle at 40% 30%,#2a82cc,#1a62a8);border:5px solid var(--white);box-shadow:0 3px 10px rgba(0,0,0,.2);color:var(--white);text-align:center}
.feature svg{position:absolute;left:93px;top:28px}
.feature h4{position:absolute;left:0;width:100%;top:90px;font-family:"Exo 2",sans-serif;font-weight:600;font-size:19px}
.feature p{position:absolute;left:28px;width:174px;top:122px;font-size:12.5px;line-height:19px;color:#dbe9f6}

/* availability */
.avail{top:2840px;height:707px}
.avail-band{left:0;top:0;width:1200px;height:540px;background:linear-gradient(180deg,#1b5c96 0%,#1f6bb0 55%,#2173b8 100%)}
.avail h2{left:0;width:1200px;top:84px;text-align:center;color:var(--white);font-size:37px}
.avail .rule{top:141px;background:var(--white)}
.calendar{position:absolute;left:217px;top:194px;width:766px;height:476px;background:var(--grey-bg);box-shadow:0 4px 16px rgba(0,0,0,.18)}
.cal-year{position:absolute;top:46px;font-family:"Exo 2",sans-serif;font-size:14px;color:var(--blue)}
.cal-month{position:absolute;left:0;width:584px;top:42px;text-align:center;font-family:"Exo 2",sans-serif;font-size:20px;color:#333;text-transform:uppercase}
.cal-grid{position:absolute;left:37px;top:122px;display:grid;grid-template-columns:repeat(7,75px);grid-auto-rows:39px;font-size:13px;color:#333;text-align:center}
.cal-grid .dh{font-family:"Exo 2",sans-serif;font-size:18px;color:#333;line-height:28px;height:49px}
.cal-grid span{display:flex;align-items:center;justify-content:center}
.cal-grid b{font-weight:400;width:26px;height:26px;border-radius:50%;display:flex;align-items:center;justify-content:center}
.cal-grid b.ok{background:var(--green);color:var(--white)}
.cal-grid b.no{background:var(--blue);color:var(--white)}
.cal-grid b.u{text-decoration:underline}
.cal-arrow{position:absolute;top:232px;width:16px;height:16px}
.cal-btn{position:absolute;top:388px;height:37px;color:var(--white);font-family:"Exo 2",sans-serif;font-weight:600;font-size:13px;line-height:37px;text-align:center;text-transform:uppercase}
.cal-side{position:absolute;left:584px;top:0;width:182px;height:476px;background:var(--white)}
.side-brand{position:absolute;left:0;width:100%;top:36px;text-align:center}
.side-brand i{display:block;width:30px;height:30px;border-radius:50%;background:var(--blue);margin:0 auto 6px}
.side-brand span{font-family:"Exo 2",sans-serif;font-weight:700;font-size:15px;color:var(--blue);text-transform:uppercase}
.side-item{position:absolute;left:26px;width:124px;font-family:"Exo 2",sans-serif;font-size:12.5px;color:var(--blue);padding-bottom:6px;border-bottom:2px solid #555}
.side-x{position:absolute;left:152px;top:132px;width:10px;height:10px;border-radius:50%;background:#e5474f}
.side-more{position:absolute;left:26px;top:400px;width:79px;height:26px;background:var(--blue);color:var(--white);font-family:"Exo 2",sans-serif;font-size:10px;line-height:26px;text-align:center;text-transform:uppercase}
.side-go{position:absolute;left:118px;top:400px;width:26px;height:26px;background:var(--blue);display:flex;align-items:center;justify-content:center}

/* news */
.news{top:3547px;height:629px}
.news h2{left:0;width:1200px;top:46px;text-align:center;font-size:37px}
.news .rule{top:105px}
.post{position:absolute;top:158px;width:296px;height:368px;background:var(--white);box-shadow:0 2px 10px rgba(0,0,0,.18);text-align:center}
.post-photo{position:absolute;left:0;top:0;width:296px;height:182px}
.post-date{position:absolute;left:8px;top:8px;width:46px;height:40px;background:var(--blue-dark);color:var(--white);font-family:"Exo 2",sans-serif;font-weight:600;font-size:11px;line-height:16px;padding-top:4px}
.post h3{position:absolute;left:0;width:100%;top:205px;font-family:"Exo 2",sans-serif;font-weight:600;font-size:18px;color:var(--ink)}
.post p{position:absolute;left:26px;width:244px;top:256px;font-size:13.5px;line-height:21px;color:#444}

/* footer */
.footer{top:4176px;height:560px;background:var(--footer);color:#ddd}
.foot-brand{left:143px;top:90px;width:195px;text-align:center}
.foot-brand i{display:block;width:70px;height:70px;border-radius:50%;background:var(--blue);margin:0 auto 10px}
.foot-brand span{font-family:"Exo 2",sans-serif;font-weight:700;font-size:24px;color:var(--blue);text-transform:uppercase;line-height:1.05;display:block}
.socials{left:173px;top:248px;display:flex;gap:8px}
.socials span{width:27px;height:27px;border-radius:50%;border:2px solid #ccc}
.footer h3{position:absolute;top:70px;font-family:"Exo 2",sans-serif;font-weight:600;font-size:22px;color:var(--white);text-transform:uppercase}
.field{position:absolute;left:386px;width:358px;height:29px;background:var(--white);font-size:12px;color:#333;padding:7px 14px}
.send{position:absolute;left:386px;top:333px;width:211px;height:37px;background:var(--blue);color:var(--white);font-family:"Exo 2",sans-serif;font-weight:600;font-size:14px;line-height:37px;text-align:center;text-transform:uppercase}
.contact{position:absolute;left:797px;display:flex;gap:14px;font-size:14px;line-height:19px;color:#ddd}
.contact svg{flex:none;margin-top:2px}
.copyright{left:0;width:1200px;top:490px;text-align:center;font-size:14px;color:#ddd}
</style>
</head>
<body>

<header class="section hero">
  <div class="photo hero-photo" role="img" aria-label="Photo of a mountain biker on a rocky alpine trail above a lake"></div>
  <svg class="abs" style="left:0;top:0" width="1200" height="755" viewBox="0 0 1200 755" aria-hidden="true">
    <path d="M0,630 L90,660 L200,700 L330,688 L420,735 L520,718 L600,755 L700,728 L790,744 L880,705 L980,690 L1080,650 L1200,624 L1200,755 L0,755Z" fill="#fff"/>
    <path d="M0,630 L90,660 L200,700 L330,688 L420,735 L520,718 L600,755 L700,728 L790,744 L880,705 L980,690 L1080,650 L1200,624" fill="none" stroke="#1d6db7" stroke-width="7"/>
  </svg>
  <div class="abs brand"><span class="brand-dot"></span><span class="brand-name">Tall Fern<br>Bicycle Rental</span></div>
  <div class="abs tollfree">
    <span class="ico"><svg width="16" height="16" viewBox="0 0 24 24"><path d="M6.6 10.8a15 15 0 0 0 6.6 6.6l2.2-2.2a1 1 0 0 1 1-.25 11.4 11.4 0 0 0 3.6.57 1 1 0 0 1 1 1V20a1 1 0 0 1-1 1A17 17 0 0 1 3 4a1 1 0 0 1 1-1h3.5a1 1 0 0 1 1 1c0 1.25.2 2.45.57 3.57a1 1 0 0 1-.25 1z" fill="#fff"/></svg></span>
    <div><small>Toll free :</small><b>808 555 0142</b></div>
  </div>
  <div class="abs search">Search here
    <svg width="16" height="16" viewBox="0 0 24 24"><circle cx="10" cy="10" r="6" fill="none" stroke="#888" stroke-width="2"/><path d="M15 15l5 5" stroke="#888" stroke-width="2"/></svg>
  </div>
  <div class="abs signup">SIGN UP</div>
  <nav class="abs nav" style="left:0;top:97px">
    <a class="active" style="left:428px">Home</a>
    <a style="left:500px">About us</a>
    <a style="left:606px">Bicycle rental</a>
    <a style="left:755px">Offers</a>
    <a style="left:840px">Blog</a>
    <a style="left:909px">FAQ</a>
    <a style="left:965px">Contact us</a>
  </nav>
  <div class="abs hero-title">
    <h1>Tall Fern Bicycle Rental</h1>
    <p class="hero-tag">Fat tire bikes for every trail</p>
  </div>
  <div class="abs dots"><span class="on"></span><span></span><span></span></div>
</header>

<section class="section welcome">
  <div class="photo welcome-bg" role="img" aria-label="Soft misty mountain landscape background"></div>
  <div class="abs welcome-mark">Tall<br>Fern</div>
  <h2 class="abs heading">Welcome to<span>Tall Fern Bicycle Rental</span></h2>
  <div class="rule"></div>
  <p class="abs">Sed ut perspiciatis unde omnis iste natus error sit voluptatem accusantium doloremque laudantium, totam rem aperiam, eaque ipsa quae ab illo inventore veritatis et quasi architecto beatae vitae dicta sunt explicabo. Nemo enim ipsam voluptatem quia voluptas sit aspernatur aut odit aut fugit, sed quia consequuntur magni dolores eos qui ratione voluptatem sequi nesciunt. Neque porro quisquam est, qui dolorem ipsum quia dolor sit amet</p>
  <div class="btn-outline">Read more</div>
</section>

<section class="section rentals">
  <div class="photo rentals-photo" role="img" aria-label="Faint photo of mountain bikers on a trail"></div>
  <h2 class="abs heading">Bicycle rental</h2>

  <article class="card" style="left:132px">
    <div class="card-photo" style="background:linear-gradient(180deg,#d9c9a0,#9aa86a 60%,#6b7a4a)" role="img" aria-label="Photo of a woman riding a bicycle on a country road"></div>
    <div class="card-icon"><svg width="24" height="16" viewBox="0 0 24 16"><circle cx="5" cy="11" r="4" fill="none" stroke="#fff" stroke-width="1.6"/><circle cx="19" cy="11" r="4" fill="none" stroke="#fff" stroke-width="1.6"/><path d="M5 11l4-7h6l4 7M9 4l3 7 3-7" fill="none" stroke="#fff" stroke-width="1.6"/></svg></div>
    <h3>NEMO ENIM IPSAM</h3>
    <div class="price">$4/HOUR*</div>
    <p>Sed ut perspiciatis unde omnis iste natus sit voluptatem accusantium doloremque laudantium</p>
    <div class="btn-outline">Book now</div>
  </article>

  <article class="card" style="left:452px">
    <div class="card-photo" style="background:linear-gradient(180deg,#8fb0c8,#5d6d7a 60%,#3c4650)" role="img" aria-label="Photo of a man in a suit riding a bicycle in the city"></div>
    <div class="card-icon"><svg width="24" height="16" viewBox="0 0 24 16"><circle cx="5" cy="11" r="4" fill="none" stroke="#fff" stroke-width="1.6"/><circle cx="19" cy="11" r="4" fill="none" stroke="#fff" stroke-width="1.6"/><path d="M5 11l4-7h6l4 7M9 4l3 7 3-7" fill="none" stroke="#fff" stroke-width="1.6"/></svg></div>
    <h3>NEMO ENIM IPSAM</h3>
    <div class="price">$4/HOUR*</div>
    <p>Sed ut perspiciatis unde omnis iste natus sit voluptatem accusantium doloremque laudantium</p>
    <div class="btn-outline">Book now</div>
  </article>

  <article class="card" style="left:772px">
    <div class="card-photo" style="background:linear-gradient(180deg,#5a6b3c,#3d4d2a 60%,#77913e)" role="img" aria-label="Photo of a cyclist with a mountain bike in a sunlit forest"></div>
    <div class="card-icon"><svg width="24" height="16" viewBox="0 0 24 16"><circle cx="5" cy="11" r="4" fill="none" stroke="#fff" stroke-width="1.6"/><circle cx="19" cy="11" r="4" fill="none" stroke="#fff" stroke-width="1.6"/><path d="M5 11l4-7h6l4 7M9 4l3 7 3-7" fill="none" stroke="#fff" stroke-width="1.6"/></svg></div>
    <h3>NEMO ENIM IPSAM</h3>
    <div class="price">$4/HOUR*</div>
    <p>Sed ut perspiciatis unde omnis iste natus sit voluptatem accusantium doloremque laudantium</p>
    <div class="btn-outline">Book now</div>
  </article>

  <svg class="abs" style="left:0;top:645px" width="1200" height="130" viewBox="0 0 1200 130" aria-hidden="true">
    <path d="M0,30 L80,22 L200,46 L330,40 L450,70 L520,60 L600,128 L680,65 L760,76 L880,40 L1000,46 L1120,20 L1200,30 L1200,130 L0,130Z" fill="#fff"/>
  </svg>
</section>

<section class="section why">
  <div class="photo why-bg" role="img" aria-label="Misty sky fading into rocky mountain peaks"></div>
  <div class="photo why-rider" role="img" aria-label="Photo of a mountain biker jumping off a rock"></div>
  <h2 class="abs heading">Why Tall Fern Bicycle Rental?</h2>
  <p class="abs sub">We simplified Bicycle rentals, so you can focus on what's important to you.</p>
  <div class="rule"></div>

  <div class="feature" style="left:134px;top:253px">
    <svg width="54" height="48" viewBox="0 0 54 48" fill="none" stroke="#fff" stroke-width="2.5"><path d="M8 34C6 18 16 8 30 8s20 10 18 24l-8 6H14z"/><path d="M24 20h16l2 10H26z"/></svg>
    <h4>Safety</h4>
    <p>Nemo enim ipsam voluptatem quia voluptas sit aspernatur aut odit aut fugit, sed quia conquuntur magni</p>
  </div>
  <div class="feature" style="left:365px;top:297px">
    <svg width="54" height="52" viewBox="0 0 54 52" fill="none" stroke="#fff" stroke-width="2.5"><path d="M27 40C17 28 14 22 14 16a13 13 0 0 1 26 0c0 6-3 12-13 24z"/><circle cx="27" cy="16" r="5"/><path d="M8 48h38l-6-10M14 38l-6 10"/></svg>
    <h4>Pit stops</h4>
    <p>Nemo enim ipsam voluptatem quia voluptas sit aspernatur aut odit aut fugit, sed quia conquuntur magni</p>
  </div>
  <div class="feature" style="left:597px;top:253px">
    <svg width="54" height="48" viewBox="0 0 54 48" fill="none" stroke="#fff" stroke-width="2.5"><rect x="6" y="14" width="40" height="28" rx="3"/><path d="M12 14l18-10 6 10"/><rect x="32" y="22" width="14" height="11" rx="2"/></svg>
    <h4>Wallet's BFF</h4>
    <p>Nemo enim ipsam voluptatem quia voluptas sit aspernatur aut odit aut fugit, sed quia conquuntur magni</p>
  </div>
  <div class="feature" style="left:828px;top:297px">
    <svg width="56" height="52" viewBox="0 0 56 52" fill="none" stroke="#fff" stroke-width="2.5"><circle cx="12" cy="38" r="9"/><circle cx="42" cy="38" r="9"/><path d="M12 38l9-14h14l7 14M21 24l6 14 8-14"/><path d="M40 4v18"/></svg>
    <h4>Bicycle Rental</h4>
    <p>Nemo enim ipsam voluptatem quia voluptas sit aspernatur aut odit aut fugit, sed quia conquuntur magni</p>
  </div>
</section>

<section class="section avail">
  <div class="abs avail-band"></div>
  <svg class="abs" style="left:0;top:430px" width="1200" height="120" viewBox="0 0 1200 120" aria-hidden="true">
    <path d="M0,80 L120,70 L240,100 L380,88 L520,110 L600,96 L720,112 L860,86 L1000,100 L1100,70 L1200,76 L1200,120 L0,120Z" fill="#fff"/>
  </svg>
  <h2 class="abs heading">Bicycle rental availability</h2>
  <div class="rule"></div>

  <div class="calendar">
    <span class="cal-year" style="left:56px">2019</span>
    <div class="cal-month">March, 2020</div>
    <span class="cal-year" style="left:490px">2021</span>
    <div class="cal-grid">
      <span class="dh">SUN</span><span class="dh">MON</span><span class="dh">TUE</span><span class="dh">WED</span><span class="dh">THUR</span><span class="dh">FRI</span><span class="dh">SAT</span>
      <span><b>1</b></span><span><b>2</b></span><span><b>3</b></span><span><b>4</b></span><span><b>5</b></span><span><b class="ok">6</b></span><span><b>7</b></span>
      <span><b>8</b></span><span><b class="ok">9</b></span><span><b>10</b></span><span><b class="no">11</b></span><span><b class="u">12</b></span><span><b>13</b></span><span><b>14</b></span>
      <span><b>15</b></span><span><b>16</b></span><span><b>17</b></span><span><b>18</b></span><span><b class="ok">19</b></span><span><b>20</b></span><span><b>21</b></span>
      <span><b>22</b></span><span><b class="no">23</b></span><span><b class="u">24</b></span><span><b>25</b></span><span><b>26</b></span><span><b>27</b></span><span><b class="u">28</b></span>
      <span><b>29</b></span><span><b>30</b></span><span><b>31</b></span>
    </div>
    <svg class="cal-arrow" style="left:30px" width="16" height="16" viewBox="0 0 16 16"><circle cx="8" cy="8" r="8" fill="#333"/><path d="M9.5 4.5L6 8l3.5 3.5" stroke="#fff" stroke-width="1.6" fill="none"/></svg>
    <svg class="cal-arrow" style="left:539px" width="16" height="16" viewBox="0 0 16 16"><circle cx="8" cy="8" r="8" fill="#333"/><path d="M6.5 4.5L10 8l-3.5 3.5" stroke="#fff" stroke-width="1.6" fill="none"/></svg>
    <div class="cal-btn" style="left:64px;width:112px;background:var(--green)">Available</div>
    <div class="cal-btn" style="left:193px;width:119px;background:var(--blue)">Cancelled</div>

    <aside class="cal-side">
      <div class="side-brand"><i></i><span>Tall Fern</span></div>
      <div class="side-x"></div>
      <div class="side-item" style="top:138px">NEMO ENIM IPSAM</div>
      <div class="side-item" style="top:187px">NEMO ENIM IPSAM</div>
      <div class="side-item" style="top:236px">NEMO ENIM IPSAM</div>
      <div class="side-item" style="top:284px">NEMO ENIM IPSAM</div>
      <div class="side-item" style="top:332px">NEMO ENIM IPSAM</div>
      <div class="side-more">Read more</div>
      <div class="side-go"><svg width="10" height="10" viewBox="0 0 10 10"><circle cx="5" cy="5" r="4" fill="#fff"/></svg></div>
    </aside>
  </div>
</section>

<section class="section news">
  <h2 class="abs heading">Laest news</h2>
  <div class="rule"></div>

  <article class="post" style="left:134px">
    <div class="post-photo" style="background:linear-gradient(180deg,#7fa8cf,#7d9a55 55%,#8b8b86)" role="img" aria-label="Photo of a group of cyclists on a road through green trees"></div>
    <div class="post-date">OCT 01<br>2019</div>
    <h3>Nemo enim ipsam volup</h3>
    <p>Sed ut perspiciatis unde omnis iste natus error sit voluptatem accustium dlorue laudantium, totam rem apiam, eaque ipsa quae</p>
  </article>
  <article class="post" style="left:452px">
    <div class="post-photo" style="background:linear-gradient(180deg,#9fb6c7,#6d7b83 55%,#4a4f52)" role="img" aria-label="Photo of a road cyclist riding along a coastal road"></div>
    <div class="post-date">OCT 01<br>2019</div>
    <h3>Nemo enim ipsam volup</h3>
    <p>Sed ut perspiciatis unde omnis iste natus error sit voluptatem accustium dlorue laudantium, totam rem apiam, eaque ipsa quae</p>
  </article>
  <article class="post" style="left:768px">
    <div class="post-photo" style="background:linear-gradient(180deg,#8d9aa3,#4a4f54 55%,#2f3336)" role="img" aria-label="Photo of cyclists riding in a painted bike lane"></div>
    <div class="post-date">OCT 01<br>2019</div>
    <h3>Nemo enim ipsam volup</h3>
    <p>Sed ut perspiciatis unde omnis iste natus error sit voluptatem accustium dlorue laudantium, totam rem apiam, eaque ipsa quae</p>
  </article>
</section>

<footer class="section footer">
  <div class="abs foot-brand"><i></i><span>Tall Fern</span></div>
  <div class="abs socials"><span></span><span></span><span></span><span></span></div>

  <h3 style="left:386px">How can we help?</h3>
  <div class="field" style="top:127px">Name</div>
  <div class="field" style="top:167px">Address</div>
  <div class="field" style="top:208px">Email</div>
  <div class="field" style="top:248px;height:70px">Comments</div>
  <div class="send">Send your enquiry</div>

  <h3 style="left:790px">Contact us</h3>
  <div class="contact" style="top:135px">
    <svg width="14" height="18" viewBox="0 0 14 18"><path d="M7 17C2 11 1 8 1 6a6 6 0 0 1 12 0c0 2-1 5-6 11z" fill="none" stroke="#ddd" stroke-width="1.5"/><circle cx="7" cy="6" r="2" fill="#ddd"/></svg>
    <div>Tall Fern Bicycle Rental<br>48 aute irure dolor in repre<br>henderit in voluptate velit</div>
  </div>
  <div class="contact" style="top:210px">
    <svg width="14" height="14" viewBox="0 0 24 24"><path d="M6.6 10.8a15 15 0 0 0 6.6 6.6l2.2-2.2a1 1 0 0 1 1-.25 11.4 11.4 0 0 0 3.6.57 1 1 0 0 1 1 1V20a1 1 0 0 1-1 1A17 17 0 0 1 3 4a1 1 0 0 1 1-1h3.5a1 1 0 0 1 1 1c0 1.25.2 2.45.57 3.57a1 1 0 0 1-.25 1z" fill="none" stroke="#ddd" stroke-width="2"/></svg>
    <div>808 555 0199</div>
  </div>
  <div class="contact" style="top:245px">
    <svg width="15" height="12" viewBox="0 0 15 12"><rect x="1" y="1" width="13" height="10" fill="none" stroke="#ddd" stroke-width="1.4"/><path d="M1 1l6.5 5L14 1" fill="none" stroke="#ddd" stroke-width="1.4"/></svg>
    <div>info@tallfernbicyclerental.com</div>
  </div>
  <div class="contact" style="top:282px">
    <svg width="14" height="18" viewBox="0 0 14 18"><path d="M7 17C2 11 1 8 1 6a6 6 0 0 1 12 0c0 2-1 5-6 11z" fill="none" stroke="#ddd" stroke-width="1.5"/><circle cx="7" cy="6" r="2" fill="#ddd"/></svg>
    <div>OPENING HOURS<br>Monday to Friday: 9.00am<br>until 6:00pm<br>Saturday: 10.00am until 2.00pm<br>Sunday : Closed</div>
  </div>

  <p class="abs copyright">Copyright © Tall Fern Bicycle Rental 2020. All rights reserved.</p>
</footer>

</body>
</html>
```